CM Candle Tube Packaging Design

Website: www.corvelmare.example
IG: @corvel.mare
Tagline: Elevate Your Ambiance
My brand is a sophisticated brand with luxury candles made of coconut wax. Im looking for an upscale minimalist chic design.
Discover the transformative power of positive energy with Corvel Mare candles. Indulge in true luxury with our specially crafted coconut wax blend that not only ignites captivating scents but also embodies modern elegance and empowering elements.
At Corvel Mare we're committed to delivering a unique and exhilarating aromatic experience to all candle lovers. Each candle is meticulously handcrafted in small batches using luxury fragrance oils exclusively formulated for coconut wax.
Our candles are:
Clean-burning
Paraben-Free
Phthalate-Free
Skin-Safe
Pet-Friendly

```html
<!DOCTYPE html>
<html lang="en">
<head>
<meta charset="utf-8">
<title>Corvel Mare — Candle Tube Label</title>
<link rel="stylesheet" href="https://fonts.googleapis.com/css2?family=Cormorant+Garamond:wght@300;400&family=Dancing+Script:wght@400&family=Tenor+Sans&display=swap">
<style>
  :root {
    --backdrop: #f3dbcf;
    --label-pink: #f8e0dc;
    --wordmark-white: #ffffff;
    --monogram-rose: #dcaaa4;
    --tagline-rose: #e5aea7;
    --claims-grey: #5b5657;
  }
  * { margin: 0; padding: 0; box-sizing: border-box; }
  html, body {
    width: 1200px;
    height: 723px;
    overflow: hidden;
    background: var(--backdrop);
  }
  .canvas {
    position: relative;
    width: 1200px;
    height: 723px;
  }
  .tube-label {
    position: absolute;
    left: 401px;
    top: 30px;
    width: 398px;
    height: 663px;
    background: var(--label-pink);
  }
  .brand-vertical {
    position: absolute;
    right: 12px;
    top: 22px;
    height: 540px;
    writing-mode: vertical-rl;
    transform: rotate(180deg);
    font-family: "Cormorant Garamond", serif;
    font-weight: 300;
    font-size: 70px;
    line-height: 1;
    letter-spacing: 4px;
    color: var(--wordmark-white);
    text-align: center;
    white-space: nowrap;
  }
  .monogram {
    position: absolute;
    left: 0;
    width: 338px;
    top: 228px;
    text-align: center;
    font-family: "Cormorant Garamond", serif;
    font-weight: 300;
    font-size: 66px;
    line-height: 1;
    color: var(--monogram-rose);
  }
  .tagline {
    position: absolute;
    left: 0;
    width: 338px;
    top: 318px;
    text-align: center;
    font-family: "Dancing Script", cursive;
    font-size: 27px;
    color: var(--tagline-rose);
    white-space: nowrap;
  }
  .claims {
    position: absolute;
    left: 0;
    right: 0;
    top: 596px;
    list-style: none;
    text-align: center;
    font-family: "Tenor Sans", sans-serif;
    font-size: 14.5px;
    line-height: 19px;
    color: var(--claims-grey);
  }
  .claims li { display: inline; margin: 0 6px; }
  .claims li::before { content: "\2022\00a0"; }
</style>
</head>
<body>
  <main class="canvas">
    <section class="tube-label">
      <div class="brand-vertical">CORVEL MARE</div>
      <div class="monogram">CM</div>
      <p class="tagline">Elevate your Ambiance</p>
      <ul class="claims">
        <li>Clean Burning</li><li>Paraben Free</li><li>Phthalate Free</li><br>
        <li>Skin Safe</li><li>Pet Friendly</li>
      </ul>
    </section>
  </main>
</body>
</html>
```